Kelbrook Plumbing flyer

I want to incorporate our logo design into a new flyer promoting the business and advertising products that we install.
We install hot water systems, Air-conditioning systems and central heating systems. Along with other aspects of plumbing such as gasfitting, roofing, sanitary and drainage
I would like the background to be the same as our business cards with the water effect and colours.

Requirements
Must have
• Logo
24/7 Emergency call out
Aspects of plumbing we do
- Hot water systems
- Central Heating
- Solar hot water systems/ heat pump systems
- Gasfitting
- Drainage
- Roofing
- Air-Conditioning
Nice to have
• Pictures of hot water systems and air-conditioning system
$30 off voucher when producing this flyer (limit 1 per house hold)

```html
<!DOCTYPE html>
<html lang="en">
<head>
<meta charset="utf-8">
<title>Kelbrook Plumbing Flyers</title>
<link href="https://fonts.googleapis.com/css2?family=Oswald:wght@500;600&family=Roboto+Condensed:wght@400;700&family=Roboto:wght@400;500;700&display=swap" rel="stylesheet">
<style>
  :root{
    --page:#e8eaed;
    --blue:#1f8fd8;
    --blue-deep:#0b5fa6;
    --sky:#3cb2ef;
    --pale:#cfe9fa;
    --dark:#26282c;
    --charcoal:#3b3e43;
    --ink:#34373c;
    --red:#e1262d;
    --white:#ffffff;
  }
  *{box-sizing:border-box;margin:0;padding:0}
  html,body{width:1200px;height:832px;overflow:hidden;background:var(--page)}
  body{position:relative;font-family:"Roboto",Arial,sans-serif;color:var(--ink)}

  .flyer{position:absolute;top:59px;width:500px;height:714px;overflow:hidden;background:var(--white);box-shadow:0 4px 14px rgba(0,0,0,.18)}
  .flyer--services{left:64px}
  .flyer--heatpump{left:636px}
  .flyer > *{position:absolute}

  .photo{left:0;top:0;width:500px;height:290px}
  .photo--plumber{background:linear-gradient(115deg,#d9dde2 0%,#a9b4c0 35%,#3f5877 62%,#1d2d45 100%)}
  .photo--house{background:linear-gradient(180deg,#7fa4c8 0%,#b9c9d8 35%,#8c8f93 62%,#4b5a3f 85%,#3a4a2f 100%)}

  .shapes{left:0;top:0;width:500px;height:714px}

  .tagline{left:0;top:25px;width:242px;height:32px;background:var(--blue);color:var(--white);font:700 22px/32px "Roboto Condensed",sans-serif;padding-left:20px;letter-spacing:.3px}
  .trades{top:72px;left:22px;list-style:none}
  .trades li{display:flex;align-items:center;gap:9px;color:var(--white);font:700 21px/25px "Roboto Condensed",sans-serif}
  .tick{width:14px;height:14px;border:2px solid var(--sky);display:inline-flex;align-items:center;justify-content:center}

  .licence{height:20px;width:200px;border-radius:10px;background:linear-gradient(90deg,var(--blue-deep),var(--sky));color:var(--white);font:700 11px/20px "Roboto",sans-serif;padding-left:16px}
  .flyer--services .licence{left:19px;top:163px}
  .flyer--heatpump .licence{left:22px;top:384px;text-align:center;padding-left:0}

  .badge{width:140px;height:140px}
  .flyer--services .badge{left:341px;top:222px}
  .flyer--heatpump .badge{left:348px;top:222px}

  .brand{left:22px;top:284px;display:flex;gap:10px;align-items:flex-start}
  .brand-dot{width:40px;height:40px;border-radius:50%;background:var(--sky);margin-top:4px}
  .brand-name{color:var(--blue);font:700 27px/25px "Roboto Condensed",sans-serif;text-transform:uppercase;letter-spacing:.2px}
  .brand-phone{color:var(--blue);font:700 17px/20px "Roboto Condensed",sans-serif;margin-top:4px;letter-spacing:.5px}

  .services{left:22px;top:382px;list-style:none}
  .services li{display:flex;align-items:center;gap:10px;height:36px;font:700 12px/14px "Roboto",sans-serif;color:var(--charcoal);text-transform:uppercase}
  .services svg{flex:none}

  .panel-head{left:262px;top:366px;width:226px;text-align:right;font:600 15.5px/18px "Oswald",sans-serif;color:var(--white);letter-spacing:.2px}
  .panel-head .accent{color:var(--sky)}
  .panel-copy{left:262px;top:428px;width:226px;font:400 10.4px/13.2px "Roboto",sans-serif;color:#e6e8ea;text-align:justify}

  .round-photo{width:108px;height:108px;border-radius:50%;border:4px solid var(--white);top:518px}
  .round-photo--heater{left:268px;background:radial-gradient(circle at 45% 40%,#f4f4f4,#b9bdc2 70%,#8d9297)}
  .round-photo--truck{left:384px;background:linear-gradient(180deg,#c9d8e6 0%,#e8ecef 40%,#7f9a5c 75%,#5b7740 100%)}

  .contact{right:14px;top:648px;text-align:right}
  .contact-phone{display:flex;align-items:center;justify-content:flex-end;gap:8px;color:var(--sky);font:700 25px/28px "Roboto Condensed",sans-serif}
  .contact-web{color:var(--white);font:500 12px/16px "Roboto",sans-serif;margin-top:8px}

  .product{left:252px;top:168px;width:200px;height:272px}
  .product-tank{position:absolute;left:0;top:0;width:120px;height:260px;border-radius:18px 18px 8px 8px;background:linear-gradient(90deg,#cfd2d4,#f7f7f5 45%,#d9dbdc)}
  .product-ac{position:absolute;left:96px;top:160px;width:110px;height:102px;border-radius:4px;background:linear-gradient(135deg,#f3f3f3,#c8cbce)}

  .headline{left:19px;top:420px;font:700 13.5px/16px "Roboto Condensed",sans-serif;color:var(--charcoal);text-transform:uppercase}
  .benefits{left:19px;top:446px;width:210px;list-style:none}
  .benefits li{position:relative;padding-left:13px;font:400 9.6px/11.5px "Roboto",sans-serif;color:var(--ink);margin-bottom:7.5px}
  .benefits li::before{content:"";position:absolute;left:1px;top:3px;width:5px;height:5px;border-radius:50%;background:var(--blue)}
  .explain{left:10px;top:592px;width:256px;text-align:center;font:400 9.6px/11.6px "Roboto",sans-serif;color:var(--ink)}

  .voucher{left:230px;top:464px;width:224px;height:118px;border-radius:8px;border:2px solid var(--sky);background:linear-gradient(180deg,#4a4d52,#26282c);color:var(--white);text-align:center}
  .voucher-title{font:700 21px/24px "Roboto",sans-serif;margin-top:8px;letter-spacing:.5px}
  .voucher-offer{display:flex;align-items:center;justify-content:center;gap:6px;margin-top:4px}
  .voucher-amount{font:700 40px/44px "Roboto Condensed",sans-serif;color:#e9f1f7}
  .voucher-off{font:700 24px/28px "Roboto Condensed",sans-serif;color:#e9f1f7}
  .voucher-when{font:700 10.5px/12.5px "Roboto",sans-serif;color:var(--sky);text-align:left;text-transform:uppercase}
  .voucher-limit{font:400 8.4px/10px "Roboto",sans-serif;margin-top:6px}
</style>
</head>
<body>

<section class="flyer flyer--services">
  <div class="photo photo--plumber" role="img" aria-label="Photo of a plumber holding hoses with a tool belt in a kitchen"></div>

  <svg class="shapes" viewBox="0 0 500 714" aria-hidden="true">
    <defs>
      <linearGradient id="swooshL" x1="0" x2="1"><stop offset="0" stop-color="#0b5fa6"/><stop offset="1" stop-color="#3cb2ef"/></linearGradient>
      <linearGradient id="panelL" x1="0" y1="0" x2="0" y2="1"><stop offset="0" stop-color="#4a4d52"/><stop offset="1" stop-color="#2a2c30"/></linearGradient>
    </defs>
    <path d="M0 282 C140 250 300 290 500 236 L500 714 L0 714 Z" fill="#fff"/>
    <rect x="251" y="250" width="249" height="440" fill="url(#panelL)"/>
    <path d="M0 252 C130 222 290 262 500 206 L500 232 C300 286 130 250 0 284 Z" fill="url(#swooshL)"/>
    <path d="M0 288 C130 256 300 292 500 240 L500 246 C300 298 130 262 0 294 Z" fill="#cfe9fa"/>
    <path d="M0 694 C150 684 320 650 500 636 L500 714 L0 714 Z" fill="#26282c"/>
    <path d="M0 672 C150 664 320 628 500 614 L500 636 C320 650 150 684 0 694 Z" fill="url(#swooshL)"/>
  </svg>

  <div class="tagline">NO JOB TO SMALL</div>
  <ul class="trades">
    <li><span class="tick"><svg width="10" height="10" viewBox="0 0 10 10"><path d="M1 5 L4 8 L9 1" stroke="#3cb2ef" stroke-width="2" fill="none"/></svg></span>PLUMBER</li>
    <li><span class="tick"><svg width="10" height="10" viewBox="0 0 10 10"><path d="M1 5 L4 8 L9 1" stroke="#3cb2ef" stroke-width="2" fill="none"/></svg></span>DRAINER</li>
    <li><span class="tick"><svg width="10" height="10" viewBox="0 0 10 10"><path d="M1 5 L4 8 L9 1" stroke="#3cb2ef" stroke-width="2" fill="none"/></svg></span>GASFITTER/LPG</li>
  </ul>
  <div class="licence">Licence Number: 208417</div>

  <svg class="badge" viewBox="0 0 140 140" aria-label="Emergency service 24 hours, 7 days, ready to respond">
    <defs>
      <path id="topArcL" d="M20 70 A50 50 0 0 1 120 70"/>
      <path id="botArcL" d="M12 70 A58 58 0 0 0 128 70"/>
    </defs>
    <circle cx="70" cy="70" r="69" fill="#fff"/>
    <circle cx="70" cy="70" r="65" fill="#1f8fd8"/>
    <circle cx="70" cy="70" r="45" fill="#fff"/>
    <circle cx="70" cy="70" r="41" fill="#e1262d"/>
    <text font-family="Roboto Condensed, sans-serif" font-weight="700" font-size="11" fill="#fff" letter-spacing=".6"><textPath href="#topArcL" startOffset="50%" text-anchor="middle">EMERGENCY SERVICE</textPath></text>
    <text font-family="Roboto Condensed, sans-serif" font-weight="700" font-size="11" fill="#fff" letter-spacing=".6"><textPath href="#botArcL" startOffset="50%" text-anchor="middle">READY TO RESPOND</textPath></text>
    <text x="70" y="53" text-anchor="middle" font-family="Roboto Condensed, sans-serif" font-weight="700" font-size="10" fill="#fff">24 HOURS</text>
    <text x="70" y="84" text-anchor="middle" font-family="Roboto Condensed, sans-serif" font-weight="700" font-size="31" fill="#fff">24/7</text>
    <text x="70" y="98" text-anchor="middle" font-family="Roboto Condensed, sans-serif" font-weight="700" font-size="9" fill="#fff">7 DAYS</text>
  </svg>

  <div class="brand">
    <span class="brand-dot"></span>
    <div>
      <div class="brand-name">Kelbrook<br>Plumbing</div>
      <div class="brand-phone">0400 555 182</div>
    </div>
  </div>

  <ul class="services">
    <li><svg width="32" height="32" viewBox="0 0 32 32"><circle cx="16" cy="16" r="15" fill="#1f8fd8" stroke="#cfe9fa" stroke-width="2"/><rect x="14" y="8" width="4" height="12" rx="2" fill="#fff"/><circle cx="16" cy="22" r="3.5" fill="#fff"/></svg>Hot Water Systems</li>
    <li><svg width="32" height="32" viewBox="0 0 32 32"><circle cx="16" cy="16" r="15" fill="#1f8fd8" stroke="#cfe9fa" stroke-width="2"/><path d="M16 8 V24 M9 12 L23 20 M9 20 L23 12" stroke="#fff" stroke-width="2"/></svg>Central Heating</li>
    <li><svg width="32" height="32" viewBox="0 0 32 32"><circle cx="16" cy="16" r="15" fill="#1f8fd8" stroke="#cfe9fa" stroke-width="2"/><rect x="8" y="11" width="16" height="10" fill="none" stroke="#fff" stroke-width="2"/><path d="M16 11 V21 M8 16 H24" stroke="#fff" stroke-width="1.5"/></svg>Solar Hot Water Systems/<br>Heat Pump Systems</li>
    <li><svg width="32" height="32" viewBox="0 0 32 32"><circle cx="16" cy="16" r="15" fill="#1f8fd8" stroke="#cfe9fa" stroke-width="2"/><circle cx="14" cy="14" r="5" fill="none" stroke="#fff" stroke-width="2"/><path d="M18 18 L23 23" stroke="#fff" stroke-width="2.5"/></svg>Gasfitting</li>
    <li><svg width="32" height="32" viewBox="0 0 32 32"><circle cx="16" cy="16" r="15" fill="#1f8fd8" stroke="#cfe9fa" stroke-width="2"/><rect x="7" y="13" width="18" height="6" rx="2" fill="#fff"/></svg>Drainage</li>
    <li><svg width="32" height="32" viewBox="0 0 32 32"><circle cx="16" cy="16" r="15" fill="#1f8fd8" stroke="#cfe9fa" stroke-width="2"/><path d="M7 19 L16 10 L25 19" stroke="#fff" stroke-width="3" fill="none"/></svg>Roofing</li>
    <li><svg width="32" height="32" viewBox="0 0 32 32"><circle cx="16" cy="16" r="15" fill="#1f8fd8" stroke="#cfe9fa" stroke-width="2"/><rect x="8" y="11" width="16" height="10" rx="1.5" fill="none" stroke="#fff" stroke-width="2"/><path d="M11 17 H21" stroke="#fff" stroke-width="1.5"/></svg>Air-Conditioning</li>
  </ul>

  <h2 class="panel-head">PLUMBER, GAS FITTER,<br>DRAINER, ROOF PLUMBER,<br><span class="accent">LP GAS FITTER MARLOW</span></h2>
  <p class="panel-copy">We service all plumbing and gasfitting needs and installation of air-conditioning. We clear blocked drains, install new hot water systems, central heating, new and existing homes, roofing, sanitary and drainage.</p>

  <div class="round-photo round-photo--heater" role="img" aria-label="Photo of an instantaneous gas hot water unit on a wall"></div>
  <div class="round-photo round-photo--truck" role="img" aria-label="Photo of a drainage service truck on site"></div>

  <div class="contact">
    <div class="contact-phone"><svg width="22" height="22" viewBox="0 0 22 22"><circle cx="11" cy="11" r="10.5" fill="#3cb2ef"/><path d="M7.5 6 L9.5 6 L10.3 8.6 L9 9.6 C9.7 11.2 10.8 12.3 12.4 13 L13.4 11.7 L16 12.5 L16 14.5 C16 15.3 15.3 16 14.5 16 C10.4 16 6 11.6 6 7.5 C6 6.7 6.7 6 7.5 6 Z" fill="#fff"/></svg>0400 555 182</div>
    <div class="contact-web">kelbrookplumbing.com &nbsp;|&nbsp; tom@kelbrookplumbing.com</div>
  </div>
</section>

<section class="flyer flyer--heatpump">
  <div class="photo photo--house" role="img" aria-label="Photo of a two-storey suburban house at dusk"></div>

  <svg class="shapes" viewBox="0 0 500 714" aria-hidden="true">
    <defs>
      <linearGradient id="swooshR" x1="0" x2="1"><stop offset="0" stop-color="#0b5fa6"/><stop offset="1" stop-color="#3cb2ef"/></linearGradient>
    </defs>
    <path d="M0 282 C140 250 300 290 500 236 L500 714 L0 714 Z" fill="#fff"/>
    <path d="M0 252 C130 222 290 262 500 206 L500 232 C300 286 130 250 0 284 Z" fill="url(#swooshR)"/>
    <path d="M0 288 C130 256 300 292 500 240 L500 246 C300 298 130 262 0 294 Z" fill="#cfe9fa"/>
    <path d="M0 694 C150 684 320 650 500 636 L500 714 L0 714 Z" fill="#26282c"/>
    <path d="M0 672 C150 664 320 628 500 614 L500 636 C320 650 150 684 0 694 Z" fill="url(#swooshR)"/>
  </svg>

  <div class="product">
    <div class="product-tank" role="img" aria-label="Photo of a heat pump hot water tank"></div>
    <div class="product-ac" role="img" aria-label="Photo of an outdoor air-conditioning unit"></div>
  </div>

  <svg class="badge" viewBox="0 0 140 140" aria-label="Emergency service 24 hours, 7 days, ready to respond">
    <defs>
      <path id="topArcR" d="M20 70 A50 50 0 0 1 120 70"/>
      <path id="botArcR" d="M12 70 A58 58 0 0 0 128 70"/>
    </defs>
    <circle cx="70" cy="70" r="69" fill="#fff"/>
    <circle cx="70" cy="70" r="65" fill="#1f8fd8"/>
    <circle cx="70" cy="70" r="45" fill="#fff"/>
    <circle cx="70" cy="70" r="41" fill="#e1262d"/>
    <text font-family="Roboto Condensed, sans-serif" font-weight="700" font-size="11" fill="#fff" letter-spacing=".6"><textPath href="#topArcR" startOffset="50%" text-anchor="middle">EMERGENCY SERVICE</textPath></text>
    <text font-family="Roboto Condensed, sans-serif" font-weight="700" font-size="11" fill="#fff" letter-spacing=".6"><textPath href="#botArcR" startOffset="50%" text-anchor="middle">READY TO RESPOND</textPath></text>
    <text x="70" y="53" text-anchor="middle" font-family="Roboto Condensed, sans-serif" font-weight="700" font-size="10" fill="#fff">24 HOURS</text>
    <text x="70" y="84" text-anchor="middle" font-family="Roboto Condensed, sans-serif" font-weight="700" font-size="31" fill="#fff">24/7</text>
    <text x="70" y="98" text-anchor="middle" font-family="Roboto Condensed, sans-serif" font-weight="700" font-size="9" fill="#fff">7 DAYS</text>
  </svg>

  <div class="brand">
    <span class="brand-dot"></span>
    <div>
      <div class="brand-name">Kelbrook<br>Plumbing</div>
      <div class="brand-phone">0400 555 182</div>
    </div>
  </div>
  <div class="licence">Licence Number: 208417</div>

  <h2 class="headline">The clear path to net zero energy!</h2>
  <ul class="benefits">
    <li>4x more efficient than traditional<br>electric water heater</li>
    <li>Allows use of off-peak power</li>
    <li>Greater first hour rating than all heat pump<br>water heaters</li>
    <li>Faster recovery after hot water draw</li>
    <li>Hot water production down to -20°F &amp; below</li>
    <li>Up to 175°F delivered hot water temperature</li>
  </ul>
  <p class="explain">The heat pump works like a reverse air-conditioner,<br>drawing heat energy from the atmosphere and<br>applying it to water in the tank.</p>

  <div class="voucher">
    <div class="voucher-title">VOUCHER</div>
    <div class="voucher-offer">
      <span class="voucher-amount">$30</span>
      <span class="voucher-off">OFF</span>
      <span class="voucher-when">When<br>producing<br>this flyer</span>
    </div>
    <div class="voucher-limit">(Limit 1 Per House Hold)</div>
  </div>

  <div class="contact">
    <div class="contact-phone"><svg width="22" height="22" viewBox="0 0 22 22"><circle cx="11" cy="11" r="10.5" fill="#3cb2ef"/><path d="M7.5 6 L9.5 6 L10.3 8.6 L9 9.6 C9.7 11.2 10.8 12.3 12.4 13 L13.4 11.7 L16 12.5 L16 14.5 C16 15.3 15.3 16 14.5 16 C10.4 16 6 11.6 6 7.5 C6 6.7 6.7 6 7.5 6 Z" fill="#fff"/></svg>0400 555 182</div>
    <div class="contact-web">kelbrookplumbing.com &nbsp;|&nbsp; tom@kelbrookplumbing.com</div>
  </div>
</section>

</body>
</html>
```